PostCard Design Project

I am making a mailing postcard
I am having the mailing printed using 4 color foil on certain parts.
I am looking for a design that maximizes the foil process where certain parts are done in foil to grab the customers attention (example: if there is a car on the postcard the headlights would be done in foil) .
I am targeting some industries, (auto, real estate, medical, beauty) I would like the post card to have examples of postcard ideas for 2 or 3 of these industries.
specs:
the postcard should be atleast 6.5x9 up to 8.5x11, I don't want to restrict the space for the creative as I don't want everything to look like a huge mess. both sides will be used.
the piece is a direct mail piece so it has to meet requirements of https://www.mailvantor.com/business/pdf/quick-reference-guide.pdf
text will be
"business with no limits, meet mailing with no addresses, gain new customers through "Open Porch Route Drop" reach new customers at their home without needing their address. "
I also want some current print specials I am running included.
-double your order FREE (order 500 business cards and get 1000)
-250 100lb gloss stock brochures 99.00
-business packages (cards, envelopes and letterhead) 299
-1000 flyers 140.40
-5000 postcards 179.99
A list of services
banners
booklets
brochures
business cards
calendars
catalogs
CD/DVD packages
envelopes
event tickets
flyers
hangtags
postcards
posters
presentation folders
rack cards
labels
table tents
window cling and decal
"order 24/7 orders@inkwillow.com" must be included
my logo is InkWillow will be supplied later
ive received some great designs. however Im looking for something a little more modern like some zorvel would put out. if the amount of words is too much please feel free to edit. also an idea i had for the list of services i offer is to have it transparent yet readable as the background of the postcard some small some big but covering the entire backgroud. you can then design on top of that with other thing. just an early morning thought
Reason: I have uploaded a sketch of my idea, please take time to look at it for an accurate depiction of what im looking for. feel free to add elements that make it pop off the page
Reason: We are getting close i will be providing feed back today

```html
<!DOCTYPE html>
<html lang="en">
<head>
<meta charset="utf-8">
<title>InkWillow Postcard – Front and Back</title>
<link rel="stylesheet" href="https://fonts.googleapis.com/css2?family=Arimo:wght@400;700&display=swap">
<style>
  :root {
    --stage: #e9e6e1;
    --card-black: #0b0b0c;
    --card-charcoal: #2a2b2d;
    --brand-blue: #1e9ce0;
    --brand-lime: #b9d531;
    --ink-white: #ffffff;
    --word-grey: #3b3c3f;
    --word-grey-light: #55575b;
    --car-red: #c8171c;
    --jewel-grey: #5c5d60;
    --portrait-tone: #dbe4ec;
  }
  * { box-sizing: border-box; margin: 0; padding: 0; }
  html, body { width: 1200px; height: 900px; overflow: hidden; }
  body {
    background: var(--stage);
    font-family: "Arimo", Arial, sans-serif;
    display: flex;
    align-items: center;
    justify-content: center;
    gap: 22px;
  }
  .postcard {
    position: relative;
    width: 570px;
    height: 380px;
    overflow: hidden;
    background: linear-gradient(135deg, var(--card-black) 0%, var(--card-charcoal) 55%, var(--card-black) 100%);
    box-shadow: 0 10px 28px rgba(0,0,0,.35);
  }

  /* brand name */
  .brand-name {
    position: absolute;
    color: var(--ink-white);
    font-weight: 700;
    letter-spacing: .2px;
    white-space: nowrap;
  }

  /* ---------- front ---------- */
  .front .brand-name { top: 20px; right: 22px; font-size: 24px; }
  .front .offer-strip {
    position: absolute; right: 0; top: 150px; width: 70px; height: 112px;
    background: var(--brand-blue);
  }
  .front .showcase { position: absolute; }
  .showcase.auto { left: 252px; top: 92px; width: 118px; height: 160px;
    background: linear-gradient(160deg, #e02a2e 0%, var(--car-red) 55%, #3a0a0b 100%); }
  .showcase.jewellery { left: 352px; top: 58px; width: 218px; height: 92px;
    background: linear-gradient(120deg, #3a3b3e 0%, var(--jewel-grey) 55%, #8d8f93 100%); }
  .showcase.beauty { left: 370px; top: 150px; width: 160px; height: 100px;
    background: linear-gradient(180deg, #b58a70 0%, var(--portrait-tone) 60%, #f4f6f8 100%); }

  .headline {
    position: absolute; left: 22px; top: 112px;
    color: var(--brand-blue); font-weight: 700; text-transform: uppercase;
    font-size: 28px; line-height: 30px; letter-spacing: .5px;
  }
  .headline .accent { font-size: 40px; line-height: 44px; }
  .specials {
    position: absolute; left: 26px; top: 272px; list-style: none;
    color: var(--ink-white); font-size: 10.5px; line-height: 14px;
  }
  .specials li { padding-left: 13px; position: relative; }
  .specials li::before { content: "\2714"; position: absolute; left: 0; font-size: 9px; }
  .specials .detail { display: block; }

  .order-band {
    position: absolute; left: 250px; right: 0; bottom: 0; height: 96px;
    background: var(--brand-blue);
    color: var(--ink-white); font-weight: 700;
    padding: 24px 0 0 22px;
  }
  .order-band .hours { font-size: 20px; line-height: 24px; }
  .order-band .email { font-size: 21px; line-height: 26px; }

  /* ---------- back ---------- */
  .back { background: linear-gradient(180deg, var(--card-black) 0%, #151517 40%, #3a3b3e 62%, #161617 80%, var(--card-black) 100%); }
  .service-cloud {
    position: absolute; left: -40px; top: 92px; width: 720px;
    font-size: 21px; line-height: 24px; font-weight: 700;
    color: var(--word-grey); white-space: nowrap;
  }
  .service-cloud .row:nth-child(odd) { color: var(--word-grey-light); }
  .service-cloud .blue { color: var(--brand-blue); }
  .service-cloud .lime { color: var(--brand-lime); }
  .back .brand-name { left: 22px; bottom: 18px; font-size: 28px; }
  .postage-box {
    position: absolute; top: 18px; right: 22px; width: 76px; height: 52px;
    background: var(--ink-white); color: #222;
    font-size: 10px; line-height: 12px; text-align: center;
    display: flex; align-items: center; justify-content: center;
  }
  .sample-badge {
    position: absolute; width: 92px; height: 92px; border-radius: 50%;
    background: var(--ink-white);
    border: 4px solid var(--brand-blue);
    box-shadow: 0 0 0 3px var(--brand-lime), 0 4px 10px rgba(0,0,0,.5);
    padding: 8px;
  }
  .sample-badge span { display: block; width: 100%; height: 100%; border-radius: 50%; }
  .sample-badge.medical { left: 330px; top: 60px; }
  .sample-badge.medical span { background: linear-gradient(135deg, #e8f0f3, #7fb9a8); }
  .sample-badge.media { left: 450px; top: 110px; }
  .sample-badge.media span { background: linear-gradient(135deg, #f2c230, #2d8bd0 60%, #d9dde2); }
  .sample-badge.realty { left: 270px; top: 170px; }
  .sample-badge.realty span { background: linear-gradient(135deg, #c33b8e, #eef0f4 60%); }
</style>
</head>
<body>

  <section class="postcard front" aria-label="Postcard front">
    <div class="offer-strip"></div>
    <div class="showcase jewellery" role="img" aria-label="Jewellery advertisement sample with rings and bracelet"></div>
    <div class="showcase auto" role="img" aria-label="Red sports car front with headlight, auto industry sample"></div>
    <div class="showcase beauty" role="img" aria-label="Beauty and dental advertisement sample with smiling model"></div>
    <div class="brand-name">InkWillow</div>

    <h1 class="headline">Let us<br>help your<br>buissness<br><span class="accent">Shine !</span></h1>

    <ul class="specials">
      <li>Double your order FREE<span class="detail">(order 500 business cards and get 1000)</span></li>
      <li>250 100lb gloss stock brochures 99.00</li>
      <li>Business packages<span class="detail">(cards, envelopes and letterhead) 299</span></li>
      <li>1000 flyers 140.40</li>
      <li>5000 postcards 179.99</li>
    </ul>

    <div class="order-band">
      <p class="hours">24 hr/7 Day</p>
      <p class="email">orders@inkwillow.com</p>
    </div>
  </section>

  <section class="postcard back" aria-label="Postcard back">
    <div class="service-cloud" aria-label="List of print services">
      <p class="row">banners • booklets • brochures • business cards • CD/DVD packages</p>
      <p class="row">booklets • brochures • calendars • catalogs • event tickets</p>
      <p class="row">brochures • <span class="blue">business cards</span> • catalogs • envelopes</p>
      <p class="row">business cards • <span class="lime">CD/DVD packages</span> • envelopes • hangtags</p>
      <p class="row">calendars • <span class="blue">envelopes</span> • <span class="blue">event tickets</span> • postcards</p>
      <p class="row"><span class="lime">catalogs</span> • <span class="blue">flyers</span> • <span class="lime">hangtags</span> • posters • <span class="blue">presentation folders</span></p>
      <p class="row">CD/DVD packages • <span class="blue">postcards</span> • <span class="lime">rack cards</span> • labels • table tents</p>
      <p class="row">envelopes • <span class="lime">posters</span> • <span class="blue">labels</span> • <span class="lime">table tents</span> • <span class="blue">window cling and decal</span></p>
      <p class="row">event tickets • presentation folders • rack cards • labels</p>
      <p class="row">flyers • hangtags • postcards • table tents • window cling</p>
      <p class="row">window cling and decal • banners • booklets</p>
    </div>

    <div class="postage-box">Postage<br>Stamp</div>
    <div class="sample-badge medical"><span role="img" aria-label="Medical brochure sample"></span></div>
    <div class="sample-badge media"><span role="img" aria-label="CD and DVD package samples"></span></div>
    <div class="sample-badge realty"><span role="img" aria-label="Flyer and presentation folder sample"></span></div>

    <div class="brand-name">InkWillow</div>
  </section>

</body>
</html>
```